RevelHubQZ Business Cards

Front
Has logo with a design. Website address (www.revelhubqz-example.net)
Has slogan (discover the nightlife)
Has phone number (5182297734)
Should be bold and stands out.

Back
Has details about what we offer.

Events
Search upcoming events
Submit events
Party Image Gallery
View and download HQ party images
Sign up as a contributing event photographer and get paid!
Tickets
Sell your event tickets online for free!
Direct pay
No ticket fee

Target Market(s)

These cards will be handed out in clubs and events to patrons.

Industry/Entity Type

Business

Contact Information for Business Card

Should match or mirror our website in some sort of way. Visit the website to get ideas.

Requirements
Must have
• Must be designed for a 3x3 inch card.

```html
<!DOCTYPE html>
<html lang="en">
<head>
<meta charset="utf-8">
<title>RevelHubQZ Business Cards</title>
<link rel="stylesheet" href="https://fonts.googleapis.com/css2?family=Quicksand:wght@400;500;700&display=swap">
<style>
  :root {
    --page: #e0e0de;
    --card: #232323;
    --cyan: #2bbef0;
    --pink: #d63a7c;
    --ink: #ffffff;
    --ink-soft: #e6e6e6;
  }
  html, body {
    margin: 0;
    width: 1200px;
    height: 659px;
    overflow: hidden;
    background: var(--page);
    font-family: "Quicksand", sans-serif;
  }
  .sheet { position: relative; width: 1200px; height: 659px; }
  .card {
    position: absolute;
    top: 142px;
    width: 375px;
    height: 374px;
    background: var(--card);
    color: var(--ink);
    text-align: center;
    overflow: hidden;
  }
  .card-front { left: 201px; }
  .card-back { left: 623px; }

  .brand-mark {
    position: absolute;
    left: 50%;
    top: 36px;
    width: 64px;
    height: 64px;
    margin-left: -32px;
    border-radius: 50%;
    background: var(--cyan);
  }
  .brand-name {
    position: absolute;
    left: 0; right: 0;
    top: 118px;
    margin: 0;
    font-size: 28px;
    font-weight: 500;
    color: var(--cyan);
    letter-spacing: 0.5px;
  }
  .brand-slogan {
    position: absolute;
    left: 0; right: 0;
    top: 152px;
    margin: 0;
    font-size: 8.5px;
    letter-spacing: 4px;
    color: var(--ink-soft);
  }
  .name-band {
    position: absolute;
    left: 0; right: 0;
    top: 189px;
    height: 59px;
    background: var(--cyan);
  }
  .person-name {
    margin: 10px 0 0;
    font-size: 20px;
    font-weight: 700;
  }
  .person-role {
    margin: 1px 0 0;
    font-size: 12px;
    font-weight: 500;
  }
  .contact {
    position: absolute;
    left: 0; right: 0;
    top: 268px;
    margin: 0;
    font-style: normal;
    font-size: 14px;
    font-weight: 500;
    line-height: 17px;
  }
  .offer-band {
    position: absolute;
    left: 0; right: 0;
    top: 38px;
    height: 30px;
    background: var(--cyan);
  }
  .offer-title {
    margin: 0;
    line-height: 30px;
    font-size: 16px;
    font-weight: 700;
    letter-spacing: 0.5px;
  }
  .offer-list {
    position: absolute;
    left: 0; right: 0;
    top: 86px;
    margin: 0;
    padding: 0;
    list-style: none;
    font-size: 14px;
    font-weight: 500;
    line-height: 21.5px;
  }
  .level-strip {
    position: absolute;
    left: 0; right: 0;
    bottom: 0;
    height: 32px;
    background: linear-gradient(to bottom, var(--pink) 0%, var(--pink) 35%, var(--cyan) 45%, var(--cyan) 100%);
    opacity: 0.9;
  }
</style>
</head>
<body>
<div class="sheet">
  <section class="card card-front">
    <div class="brand-mark"></div>
    <h1 class="brand-name">RevelHubQZ</h1>
    <p class="brand-slogan">discover the nightlife</p>
    <div class="name-band">
      <p class="person-name">Dana Reyes</p>
      <p class="person-role">Managing Director</p>
    </div>
    <address class="contact">
      5182297734<br>
      support@revelhubqz-example.net<br>
      www.revelhubqz-example.net
    </address>
    <div class="level-strip" role="img" aria-label="Row of pink and blue sound level bars"></div>
  </section>

  <section class="card card-back">
    <div class="offer-band"><h2 class="offer-title">WE OFFER</h2></div>
    <ul class="offer-list">
      <li>Events</li>
      <li>Search upcoming events</li>
      <li>Submit events</li>
      <li>Party Image Gallery</li>
      <li>View and download HQ party images</li>
      <li>Sign up as a contributing event</li>
      <li>photographer and get paid!</li>
      <li>Tickets</li>
      <li>Sell your event tickets online for free!</li>
      <li>Direct pay</li>
      <li>No ticket fee</li>
    </ul>
    <div class="level-strip" role="img" aria-label="Row of pink and blue sound level bars"></div>
  </section>
</div>
</body>
</html>
```